Substance abuse awareness flyer for school age kids

I am needing a flyer for school-age kids. What if it were designed to look like an Quorby with someone texting and the text bubbles were some of the text below with emojis? Maybe a text chain between to friends:

Maybe the first text bubble says "I'm thinking about using drugs and alcohol"
the next bubble: "Just say no!" ( perhaps a stop sign emoji ?)

"Talk to your parents, your teachers at school, or your doctor about how drugs and alcohol can harm you"

another text bubble "did you know that alcohol and drugs could lead to..."
then include some of the info below (see links for more info).
Where ever you get info, it must be cited.

this needs to be English on one side and Spanish on the other side and needs to include the logo attached.

The effects of substance abuse
RMQ: https://www.rmqhealthnet.org/plwtrk/vesk/features/teen-substance-use.html
Affect growth and development, especially brain development. Not able to focus at school or be around friends. https://www.halvenstudy.org/sites/default/files/youthguide_2.pdf
Leads to risky behaviors and lack of impulse control (dangerous activities) https://www.halvenstudy.org/sites/default/files/youthguide_2.pdf
Contribute to health problems as an adult: heart disease, high blood pressure, and trouble sleeping.

Target Market(s)

school age kids 9-20

Requirements
Must have
• Print ready: 8.5x11

```html
<!DOCTYPE html>
<html lang="en">
<head>
<meta charset="UTF-8">
<title>Substance Use Awareness Flyer</title>
<link rel="stylesheet" href="https://fonts.googleapis.com/css2?family=Montserrat:wght@500;600;700;800&display=swap">
<style>
  :root {
    --page-bg: #9aa9b1;
    --sky-blue: #0e75bd;
    --bubble-blue: #72cbe0;
    --bubble-green: #bdd532;
    --maroon: #5e2233;
    --ink: #141414;
    --body-ink: #2a2a2a;
    --white: #ffffff;
    --ring-blue: #5ab4e0;
  }
  * { margin: 0; padding: 0; box-sizing: border-box; }
  html, body {
    width: 1029px; height: 1200px; overflow: hidden;
    background: var(--page-bg);
    font-family: "Montserrat", Arial, sans-serif;
  }
  .flyer {
    position: absolute; left: 72px; top: 18px;
    width: 884px; height: 1164px;
    background: var(--white);
    overflow: hidden;
  }
  .flyer-art { position: absolute; inset: 0; width: 884px; height: 1164px; }
  .bubble-text {
    position: absolute; color: var(--ink); font-weight: 700;
  }
  .bubble-thinking {
    left: 128px; top: 54px; font-size: 18.5px; line-height: 22px;
    font-weight: 800; letter-spacing: 0.4px; text-transform: uppercase;
  }
  .bubble-say-no {
    left: 438px; top: 147px; width: 213px; height: 60px;
    display: flex; align-items: center; justify-content: center;
    font-size: 23px; font-weight: 800;
  }
  .bubble-talk {
    left: 363px; top: 238px; width: 320px;
    font-size: 16.5px; line-height: 21.3px;
  }
  .bubble-facts {
    left: 265px; top: 396px; width: 372px;
    font-size: 18px; line-height: 22.8px;
  }
  .bubble-source {
    position: absolute; right: 248px; top: 538px;
    color: var(--white); font-size: 17px; font-weight: 700;
  }
  .brand-name {
    position: absolute; left: 694px; top: 73px; width: 150px;
    text-align: center; color: var(--maroon);
    font-size: 15px; line-height: 20px; font-weight: 800;
    text-transform: uppercase; letter-spacing: 0.5px;
  }
  .risks-heading {
    position: absolute; left: 0; top: 724px; width: 392px; height: 54px;
    background: var(--sky-blue); border-radius: 0 27px 27px 0;
    color: var(--white); font-size: 26px; font-weight: 800;
    display: flex; align-items: center; padding-left: 11px;
    letter-spacing: 0.2px;
  }
  .risks-list { list-style: none; position: absolute; left: 0; top: 824px; width: 884px; }
  .risks-list li {
    position: relative; padding-left: 38px;
    color: var(--body-ink); font-size: 23px; line-height: 31px; font-weight: 500;
  }
  .risks-list li::before {
    content: ""; position: absolute; left: 11px; top: 9px;
    width: 14px; height: 14px; border-radius: 50%; background: var(--sky-blue);
  }
  .risks-list li + li { margin-top: 33px; }
  .cta {
    position: absolute; left: 200px; top: 1084px; width: 480px; height: 58px;
    background: var(--sky-blue); border-radius: 29px;
    color: var(--white); font-size: 26px; font-weight: 800;
    display: flex; align-items: center; justify-content: center;
  }
</style>
</head>
<body>
<main class="flyer">
  <svg class="flyer-art" viewBox="0 0 884 1164" xmlns="http://www.w3.org/2000/svg">
    <defs>
      <linearGradient id="friend-tones" x1="0" y1="0" x2="0" y2="1">
        <stop offset="0" stop-color="#4b3496"/>
        <stop offset="0.5" stop-color="#8b6fc0"/>
        <stop offset="1" stop-color="#6a3d9e"/>
      </linearGradient>
    </defs>
    <rect class="sky" width="884" height="1164" fill="var(--sky-blue)"/>
    <path class="brand-corner" d="M767,0 L884,0 L884,119 L820,150 L767,95 Z" fill="var(--white)"/>
    <circle class="brand-disc" cx="769" cy="95" r="75" fill="var(--white)"/>
    <circle class="brand-ring" cx="769" cy="95" r="68" fill="none" stroke="var(--ring-blue)" stroke-width="1.5"/>

    <g role="img" aria-label="Illustration of a teen seen from behind, texting on a phone">
      <path d="M0,205 Q30,152 130,151 Q205,156 228,240 L236,600 L0,600 Z" fill="url(#friend-tones)"/>
    </g>

    <path class="lower-panel" d="M0,597 C200,600 330,660 424,709 C560,780 720,815 884,822 L884,1164 L0,1164 Z" fill="var(--white)"/>
    <path class="divider-curve" d="M0,597 C200,600 330,660 424,709 C560,780 720,815 884,822" fill="none" stroke="var(--maroon)" stroke-width="8"/>

    <g role="img" aria-label="Illustration of a second teen seen from behind, reading a text on a phone">
      <path d="M751,318 Q810,300 884,318 L884,810 L648,810 Q632,700 652,560 Q700,470 751,318 Z" fill="url(#friend-tones)"/>
    </g>

    <g class="bubbles">
      <rect x="112" y="39" width="325" height="81" fill="var(--bubble-green)"/>
      <polygon points="170,119 240,119 168,145" fill="var(--bubble-green)"/>
      <rect x="438" y="147" width="213" height="60" fill="var(--bubble-blue)"/>
      <polygon points="580,206 613,206 615,226" fill="var(--bubble-blue)"/>
      <rect x="337" y="227" width="356" height="107" fill="var(--bubble-blue)"/>
      <polygon points="550,333 608,333 633,368" fill="var(--bubble-blue)"/>
      <rect x="243" y="384" width="398" height="181" fill="var(--bubble-blue)"/>
      <polygon points="485,564 550,564 573,621" fill="var(--bubble-blue)"/>
    </g>
  </svg>

  <p class="bubble-text bubble-thinking">I'm thinking about using<br>drugs and alcohol</p>
  <p class="bubble-text bubble-say-no">JUST SAY NO!</p>
  <p class="bubble-text bubble-talk">Talk to your parents, your teachers at school, or your doctor about how drugs and alcohol can harm you.</p>
  <p class="bubble-text bubble-facts">Did you know that alcohol and drugs could lead to - The development of chronic diseases and other serious problems including: High blood pressure, heart disease, stroke, liver disease, and digestive problems.</p>
  <p class="bubble-source">-rmqhealthnet.org</p>

  <p class="brand-name">Pinecrest<br>Health Group</p>

  <h2 class="risks-heading">RISKS OF SUBSTANCE USE</h2>
  <ul class="risks-list">
    <li>Affect the growth and development of teens,<br>especially brain development.</li>
    <li>Occur more frequently with other risky behaviors.</li>
    <li>If you use drugs and alcohol at an early age,<br>it increases your chances of becoming addicted later in life</li>
  </ul>

  <p class="cta">Say No to Drugs and Alcohol!</p>
</main>
</body>
</html>
```